High Tech Real Estate Startup needs a business card

We are developing an innovative real estate marketing product based around advanced search and virtual reality.

We talk to people, we need business cards.

Target Market(s)

The target market is technology professionals and realtors.

Contact Information for Business Card

The information to be included will include

Name
Title
Phone Number
E-mail Address
www.zelquin.com

It should use simple iconography for each one of those fields.

Font styles to use
Other font styles liked:
• Co, Jubilat, Avenir

Colors

Designer to choose colors to be used in the design.

Requirements
Must have
• Clean aesthetic,
• Good use of negative space.
• It should use our company logo, shown in the attached file. It is able to use the negative of that logo (coloured font and white background) and I have attached other acceptable accent colours in a swatch file.
Should not have
• Should not be too busy
• No extraneous text (slogans, tag lines etc)

```html
<!DOCTYPE html>
<html lang="en">
<head>
<meta charset="utf-8">
<title>Zelquin Business Card</title>
<link rel="stylesheet" href="https://fonts.googleapis.com/css2?family=Mulish:wght@400;600;700&display=swap">
<style>
  :root {
    --bg: #3a3a3c;
    --card: #1f1f21;
    --logo-gloss: #0e0e0f;
    --teal: #3fb8ba;
    --text: #f1f1f1;
    --muted: #cfcfcf;
  }
  * { margin: 0; padding: 0; box-sizing: border-box; }
  html, body { width: 799px; height: 1200px; overflow: hidden; }
  body {
    background: var(--bg);
    font-family: "Mulish", "Avenir", sans-serif;
    display: flex;
    flex-direction: column;
    align-items: center;
    justify-content: space-around;
    padding: 90px 0;
  }
  .card {
    width: 580px;
    height: 332px;
    background: var(--card);
    border-radius: 26px;
    position: relative;
    box-shadow: 0 18px 40px rgba(0,0,0,0.35);
  }
  .card-front {
    display: flex;
    align-items: center;
    justify-content: center;
  }
  .wordmark {
    font-weight: 600;
    letter-spacing: 0.04em;
    line-height: 1;
    white-space: nowrap;
  }
  .card-front .wordmark {
    font-size: 74px;
    color: var(--logo-gloss);
  }
  .card-back .wordmark {
    position: absolute;
    left: 40px;
    top: 106px;
    font-size: 50px;
    color: var(--teal);
  }
  .contact {
    position: absolute;
    left: 330px;
    top: 182px;
  }
  .contact-name {
    font-size: 22px;
    font-weight: 700;
    color: var(--teal);
    line-height: 1.1;
    white-space: nowrap;
  }
  .contact-title {
    font-size: 13px;
    font-weight: 600;
    color: var(--muted);
    margin-top: 2px;
    margin-bottom: 10px;
  }
  .contact-list { list-style: none; }
  .contact-list li {
    display: flex;
    align-items: center;
    gap: 10px;
    font-size: 14px;
    color: var(--text);
    line-height: 20px;
    white-space: nowrap;
  }
  .contact-list .icon { width: 14px; height: 14px; flex: none; }
</style>
</head>
<body>
  <section class="card card-front">
    <div class="wordmark">ZELQUIN</div>
  </section>

  <section class="card card-back">
    <div class="wordmark">ZELQUIN</div>
    <div class="contact">
      <div class="contact-name">Alex Rowan Hale</div>
      <div class="contact-title">Managing Director</div>
      <ul class="contact-list">
        <li>
          <svg class="icon" viewBox="0 0 14 14" aria-hidden="true">
            <circle cx="7" cy="7" r="7" fill="var(--teal)"/>
            <path d="M4.3 3.6c.4-.3.8-.2 1 .2l.6 1.1c.2.4.1.7-.2.9l-.4.3c.3.8.9 1.5 1.8 1.9l.3-.4c.2-.3.6-.4.9-.2l1.1.6c.4.2.5.6.2 1-.5.8-1.3 1-2.2.6C5.4 9 4.4 7.9 3.8 6.3c-.3-1 0-2 .5-2.7z" fill="var(--card)"/>
          </svg>
          555.204.7381
        </li>
        <li>
          <svg class="icon" viewBox="0 0 14 14" aria-hidden="true">
            <circle cx="7" cy="7" r="7" fill="var(--teal)"/>
            <rect x="3.5" y="4.6" width="7" height="4.8" rx="0.6" fill="var(--card)"/>
            <path d="M3.8 5l3.2 2.4L10.2 5" stroke="var(--teal)" stroke-width="0.8" fill="none"/>
          </svg>
          alexhale@zelquin.com
        </li>
        <li>
          <svg class="icon" viewBox="0 0 14 14" aria-hidden="true">
            <circle cx="7" cy="7" r="7" fill="var(--teal)"/>
            <circle cx="7" cy="7" r="3.6" fill="none" stroke="var(--card)" stroke-width="0.9"/>
            <ellipse cx="7" cy="7" rx="1.5" ry="3.6" fill="none" stroke="var(--card)" stroke-width="0.8"/>
            <path d="M3.4 7h7.2" stroke="var(--card)" stroke-width="0.8"/>
          </svg>
          www.zelquin.com
        </li>
      </ul>
    </div>
  </section>
</body>
</html>
```